Need Business Card for our Real Estate Business with Sales Executive's Picture

PANTONE 484 C ( RED)

PANTONE 2766 C ( BLUE

Industry/Entity Type

Real Estate

Contact Information for Business Card

Name, Mobile, email, & picture of Person
Agency Phone, address, Web address

Requirements
Must have
• Our Logo Colours, Agent Picture,

```html
<!DOCTYPE html>
<html lang="en">
<head>
<meta charset="utf-8">
<title>Meridia Real Estate – Business Card</title>
<link rel="stylesheet" href="https://fonts.googleapis.com/css2?family=Roboto+Condensed:wght@700&family=Roboto:wght@400;500&display=swap">
<style>
  :root {
    --backdrop: #2b2b2d;
    --paper: #f4f4f4;
    --navy: #1b2452;
    --maroon: #7b1e22;
    --ink: #4a4a4a;
    --rule: #b9b9b9;
    --suit-light: #dfe4ef;
    --suit-dark: #2b4aa0;
  }
  * { box-sizing: border-box; margin: 0; padding: 0; }
  html, body { width: 1200px; height: 900px; overflow: hidden; }
  body {
    background: var(--backdrop);
    display: flex;
    flex-direction: column;
    align-items: center;
    justify-content: center;
    gap: 40px;
    font-family: "Roboto", Arial, sans-serif;
  }
  .card {
    position: relative;
    width: 700px;
    height: 395px;
    background: var(--paper);
    overflow: hidden;
  }

  /* Front */
  .brand {
    position: absolute;
    left: 60px;
    top: 150px;
    width: 300px;
    text-align: center;
  }
  .brand-name {
    display: flex;
    align-items: center;
    justify-content: center;
    gap: 10px;
    font-family: "Roboto Condensed", "Arial Narrow", sans-serif;
    font-weight: 700;
    font-size: 30px;
    letter-spacing: 1px;
    color: var(--navy);
    text-transform: uppercase;
  }
  .brand-mark {
    width: 14px;
    height: 14px;
    background: var(--maroon);
  }
  .brand-web {
    margin-top: 14px;
    font-size: 15px;
    letter-spacing: 5px;
    color: var(--ink);
  }
  .agent-photo {
    position: absolute;
    right: 20px;
    top: 30px;
    bottom: 0;
    width: 270px;
    background: linear-gradient(180deg, var(--suit-light) 0%, var(--suit-dark) 100%);
  }

  /* Back */
  .identity {
    position: absolute;
    right: 390px;
    top: 140px;
    text-align: right;
  }
  .person-name {
    font-family: "Roboto Condensed", "Arial Narrow", sans-serif;
    font-weight: 700;
    font-size: 34px;
    color: var(--navy);
    text-transform: uppercase;
  }
  .person-title {
    margin-top: 4px;
    font-family: "Roboto Condensed", "Arial Narrow", sans-serif;
    font-weight: 700;
    font-size: 18px;
    color: var(--maroon);
    text-transform: uppercase;
  }
  .divider {
    position: absolute;
    left: 335px;
    top: 135px;
    width: 1px;
    height: 115px;
    background: var(--rule);
  }
  .contact-list {
    position: absolute;
    left: 355px;
    top: 142px;
    list-style: none;
  }
  .contact-list li {
    display: flex;
    align-items: center;
    gap: 10px;
    font-size: 17px;
    line-height: 25px;
    color: var(--ink);
  }
  .icon { width: 15px; height: 15px; fill: var(--navy); flex: none; }
  .address {
    position: absolute;
    left: 110px;
    top: 310px;
    display: flex;
    align-items: center;
    gap: 8px;
    font-size: 18px;
    color: var(--ink);
  }
</style>
</head>
<body>

  <section class="card card-front">
    <div class="brand">
      <div class="brand-name"><span class="brand-mark"></span>Meridia Real Estate</div>
      <div class="brand-web">www.meridia.com</div>
    </div>
    <div class="agent-photo" role="img" aria-label="Portrait of the sales executive in a blue suit and striped tie"></div>
  </section>

  <section class="card card-back">
    <div class="identity">
      <div class="person-name">Daniel Brooks</div>
      <div class="person-title">CEO/Founder</div>
    </div>
    <div class="divider"></div>
    <ul class="contact-list">
      <li>
        <svg class="icon" viewBox="0 0 16 16"><path d="M3.5 1l2.5 3-1.5 2c1 2 3 4 5 5l2-1.5 3 2.5-1.5 2.5C7 15 1 9 1 2.5z"/></svg>
        555 210 4786
      </li>
      <li>
        <svg class="icon" viewBox="0 0 16 16"><path d="M4 0h8a1 1 0 011 1v14a1 1 0 01-1 1H4a1 1 0 01-1-1V1a1 1 0 011-1zm1 2v10h6V2zm3 11a1 1 0 100 2 1 1 0 000-2z"/></svg>
        555 392 6140
      </li>
      <li>
        <svg class="icon" viewBox="0 0 16 16"><path d="M0 3h16v1L8 9 0 4zm0 3l8 5 8-5v7H0z"/></svg>
        daniel@meridia.com
      </li>
      <li>
        <svg class="icon" viewBox="0 0 16 16"><circle cx="8" cy="8" r="7.5"/><path d="M1 8h14M8 .5c3 3 3 12 0 15M8 .5c-3 3-3 12 0 15" stroke="#f4f4f4" stroke-width="1" fill="none"/></svg>
        www.meridia.com
      </li>
    </ul>
    <div class="address">
      <svg class="icon" viewBox="0 0 16 16"><path d="M8 0a5.5 5.5 0 015.5 5.5C13.5 10 8 16 8 16S2.5 10 2.5 5.5A5.5 5.5 0 018 0zm0 3a2.5 2.5 0 100 5 2.5 2.5 0 000-5z"/></svg>
      1420 Juniper Court, Fairbanks, Alaska 99701
    </div>
  </section>

</body>
</html>
```